Black Matte card with samurai logo which I would like it to be textured and company name on one side and on the other side I would like the company information with the reno (Face logo) Sushi logo. Double Sided card.

majority customers are University students, University sororities and fraternities.

It Company

Reno Sushi
317 W. Harlow Ave
Tucson, AZ 85042
Phone (520)413-6271
Fax (520)357-1846
E-mail: Renosushidesert@mailbox-example.com
FB: Renosushidesert
Twitter: Renosushidesert

• Present Normal

```html
<!DOCTYPE html>
<html lang="en">
<head>
<meta charset="utf-8">
<title>Reno Sushi – Business Card</title>
<link rel="stylesheet" href="https://fonts.googleapis.com/css2?family=Open+Sans:wght@400;600&display=swap">
<style>
  :root {
    --backdrop: #e9e6e1;
    --card-black: #1c1c1c;
    --card-black-edge: #0c0c0c;
    --card-black-mid: #3a3a3a;
    --card-white: #ffffff;
    --card-border: #d8d8d8;
    --brand-red: #b8262b;
    --ink: #3a3a3a;
    --rule: #c9c9c9;
    --icon-social: #8a8a8a;
  }
  * { margin: 0; padding: 0; box-sizing: border-box; }
  html, body {
    width: 1200px; height: 386px; overflow: hidden;
    background: var(--backdrop);
    font-family: "Open Sans", Arial, sans-serif;
  }
  .canvas { position: relative; width: 1200px; height: 386px; }

  .card { position: absolute; border-radius: 28px; overflow: hidden; }

  .card--front {
    left: 22px; top: 40px; width: 568px; height: 320px;
    background:
      repeating-linear-gradient(90deg, rgba(255,255,255,0.025) 0 3px, rgba(0,0,0,0.04) 3px 7px),
      radial-gradient(ellipse at 50% 45%, var(--card-black-mid) 0%, var(--card-black) 55%, var(--card-black-edge) 100%);
  }
  .front-mark {
    position: absolute; left: 50%; top: 58px; transform: translateX(-50%);
    width: 150px; height: 150px; border-radius: 50%;
    background: var(--brand-red);
  }
  .front-name {
    position: absolute; left: 0; right: 0; top: 228px;
    text-align: center; color: var(--brand-red);
    font-size: 52px; font-weight: 400; letter-spacing: 1px; line-height: 1;
  }

  .card--back {
    left: 605px; top: 32px; width: 560px; height: 318px;
    background: var(--card-white);
    border: 1px solid var(--card-border);
  }
  .back-mark {
    position: absolute; left: 50%; top: 28px; transform: translateX(-50%);
    width: 90px; height: 90px; border-radius: 50%;
    background: var(--brand-red);
  }
  .back-name {
    position: absolute; left: 0; right: 0; top: 140px;
    text-align: center; color: var(--brand-red);
    font-size: 40px; font-weight: 400; line-height: 1; letter-spacing: 1px;
  }
  .back-rule {
    position: absolute; left: 42px; right: 42px; top: 213px; height: 2px;
    background: linear-gradient(90deg, transparent, var(--rule) 15%, var(--rule) 85%, transparent);
  }
  .contact {
    position: absolute; left: 0; right: 0; top: 222px;
    color: var(--ink); font-size: 13.5px; text-align: center; line-height: 21px;
  }
  .contact-row { display: flex; justify-content: center; align-items: center; gap: 6px; }
  .contact-row + .contact-row { margin-top: 0; }
  .contact-item { display: inline-flex; align-items: center; gap: 6px; }
  .contact-item + .contact-item { margin-left: 10px; }
  .icon { width: 12px; height: 12px; flex: none; }
  .icon--social { width: 13px; height: 13px; background: var(--icon-social); border-radius: 2px; }
  .contact-address { margin-top: 9px; }
</style>
</head>
<body>
<main class="canvas">
  <section class="card card--front" aria-label="Card front">
    <div class="front-mark" role="img" aria-label="Reno Sushi emblem area"></div>
    <p class="front-name">reno sushi</p>
  </section>

  <section class="card card--back" aria-label="Card back">
    <div class="back-mark" role="img" aria-label="Reno Sushi emblem area"></div>
    <p class="back-name">reno sushi</p>
    <div class="back-rule"></div>

    <div class="contact">
      <div class="contact-row">
        <span class="contact-item">
          <svg class="icon" viewBox="0 0 12 12" aria-hidden="true"><circle cx="6" cy="6" r="5.3" fill="none" stroke="#b8262b" stroke-width="1.2"/><path d="M4 3.2 L5.2 3 L5.6 4.6 L4.9 5.1 Q5.6 6.6 6.9 7.1 L7.4 6.4 L9 6.8 L8.8 8 Q6.6 8.4 4.8 6.6 Q3.4 5 4 3.2Z" fill="#b8262b"/></svg>
          (520)413-6271
        </span>
        <span class="contact-item">
          <svg class="icon" viewBox="0 0 12 12" aria-hidden="true"><rect x="3" y="0.5" width="6" height="11" rx="1" fill="#b8262b"/><rect x="4" y="2" width="4" height="3.5" fill="#fff"/><rect x="4" y="6.5" width="4" height="3.5" fill="#fff" opacity="0.6"/></svg>
          (520)357-1846
        </span>
      </div>
      <div class="contact-row">
        <span class="contact-item">
          <svg class="icon" viewBox="0 0 12 12" aria-hidden="true"><rect x="0.5" y="2.5" width="11" height="7.5" rx="1" fill="#b8262b"/><path d="M0.8 3 L6 7 L11.2 3" fill="none" stroke="#fff" stroke-width="1"/></svg>
          Renosushidesert@mailbox-example.com
        </span>
      </div>
      <div class="contact-row">
        <span class="contact-item"><span class="icon icon--social" aria-hidden="true"></span>Renosushidesert</span>
        <span class="contact-item"><span class="icon icon--social" aria-hidden="true"></span>Renosushidesert</span>
      </div>
      <div class="contact-row contact-address">
        Reno Sushi 317 W. Harlow Ave Tucson, AZ 85042
      </div>
    </div>
  </section>
</main>
</body>
</html>
```